Buch-/E-Book-Cover für Selfpublisher
Zielgruppe
Ich bin ein Selfpublisher. Meine Zielgruppe sind Menschen ab dem mittleren Alter.
Aufgabenstellung
Das Cover sollte nicht verspielt sein, sondern klar und nüchtern.
Es muss in Briefmarkengröße ebenso wirken wie im Mittel- und Großformat.

```html
<!DOCTYPE html>
<html lang="de">
<head>
<meta charset="utf-8">
<title>Narbe im Wolfsfell – Cover</title>
<link href="https://fonts.googleapis.com/css2?family=Playfair+Display:wght@400;700&family=Crimson+Pro:wght@300;400&display=swap" rel="stylesheet">
<style>
  :root {
    --backdrop: #d6d5d6;
    --cover-dark: #141516;
    --cover-mid: #1f2a2e;
    --cover-mist: #4f6a72;
    --cover-haze: #3a4e55;
    --title-red: #c8191e;
    --label-light: #e6e4e2;
  }
  * { margin: 0; padding: 0; box-sizing: border-box; }
  html, body {
    width: 1200px;
    height: 900px;
    overflow: hidden;
    background: var(--backdrop);
  }
  .book-cover {
    position: absolute;
    left: 317px;
    top: 50px;
    width: 566px;
    height: 800px;
    background: var(--cover-dark);
    overflow: hidden;
  }
  .cover-artwork {
    position: absolute;
    inset: 0;
    background:
      radial-gradient(ellipse 70% 30% at 50% 58%, rgba(20,21,22,0.9) 0%, rgba(20,21,22,0) 70%),
      linear-gradient(180deg,
        var(--cover-haze) 0%,
        var(--cover-mist) 22%,
        var(--cover-haze) 40%,
        var(--cover-mid) 58%,
        var(--cover-dark) 75%,
        var(--cover-dark) 100%);
  }
  .book-title { font-weight: 400; }
  .cover-text {
    position: absolute;
    left: 0;
    width: 100%;
    text-align: center;
    line-height: 1;
    white-space: nowrap;
  }
  .author-name {
    top: 172px;
    font-family: "Playfair Display", serif;
    font-weight: 700;
    font-size: 44px;
    letter-spacing: -0.8px;
    color: var(--title-red);
  }
  .title-line {
    font-family: "Playfair Display", serif;
    font-weight: 400;
    color: var(--title-red);
  }
  .title-first {
    top: 486px;
    font-size: 64px;
    letter-spacing: -0.5px;
  }
  .title-connector {
    top: 576px;
    font-family: "Crimson Pro", serif;
    font-weight: 300;
    font-size: 25px;
    letter-spacing: 6px;
    padding-left: 6px;
    color: var(--label-light);
  }
  .title-second {
    top: 618px;
    font-size: 64px;
    letter-spacing: -1px;
  }
  .genre-label {
    top: 700px;
    font-family: "Crimson Pro", serif;
    font-weight: 300;
    font-size: 26px;
    letter-spacing: 6px;
    padding-left: 6px;
    color: var(--label-light);
  }
</style>
</head>
<body>
  <main class="book-cover">
    <div class="cover-artwork" role="img" aria-label="Foto: dunkle Wolkendecke in Blaugrün über einem schattigen Berggipfel"></div>
    <p class="cover-text author-name">Konrad Falk</p>
    <h1 class="book-title">
      <span class="cover-text title-line title-first">NARBE</span>
      <span class="cover-text title-connector">IM</span>
      <span class="cover-text title-line title-second">WOLFSFELL</span>
    </h1>
    <p class="cover-text genre-label">THRILLER</p>
  </main>
</body>
</html>
```